Harborview Optical -Window Poster (Optometrist)

We are an optometry practice and we need a poster for a new store promotion for our window highlighting we now also sell 2 pairs of glasses as a package deal. The size will be 1300mm width x 1900mm height

The artwork will be displayed as a fabric banner in our shop window. We have 7 other banners with different services our business provides. The words needs to standout for passers by and the cars stopped at the traffic lights out front of our business. We already have signs with our logos phone number etc. so we won't need them included in the poster.

It would need to include the following information.

Two pair packages now available*

*Conditions apply

The artwork will be displayed as a fabric banner in our shop window. We have 7 other banners with different services our business provides. The words needs to standout for passers by and the cars stopped at the traffic lights out front of our business. We already have signs with our logos phone number etc. so we won't need them included in the poster. Thank you for your work it's amazing Added Saturday, February 18, 2017

The artwork will be displayed as a fabric banner in our shop window. We have 7 other banners with different services our business provides. The words needs to standout for passers by and the cars stopped at the traffic lights out front of our business. We already have signs with our logos phone number etc. so we won't need them included in the poster. Added Saturday, February 18, 2017

Target Market(s)

Cars driving past and stopped at traffic lights outside our store.

Industry/Entity Type

Optician

Requirements
Must have
• Poster must say:
• Two pair packages now available*
• *Conditions apply

```html
<!DOCTYPE html>
<html lang="en">
<head>
<meta charset="utf-8">
<title>Harborview Optical – Two Pair Packages Window Poster</title>
<link href="https://fonts.googleapis.com/css2?family=Archivo+Black&family=Anton&display=swap" rel="stylesheet">
<style>
  :root {
    --poster-dark: #1c1a19;
    --poster-mid: #2f2826;
    --photo-warm: #4a3733;
    --photo-deep: #2a2120;
    --headline-white: #f4f4f4;
    --promo-red: #e0242b;
    --promo-yellow: #f7ec13;
    --sticker-ink: #141414;
  }
  * { margin: 0; padding: 0; box-sizing: border-box; }
  html, body {
    width: 962px;
    height: 1200px;
    overflow: hidden;
    background: var(--poster-dark);
  }
  .poster {
    position: relative;
    width: 962px;
    height: 1200px;
    overflow: hidden;
    background: var(--poster-dark);
  }
  .poster__backdrop {
    position: absolute;
    inset: 0;
    background:
      radial-gradient(ellipse 50% 25% at 55% 96%, rgba(80, 60, 55, 0.35), transparent 70%),
      linear-gradient(180deg, #232020 0%, var(--poster-mid) 45%, #262120 75%, #1d1a1a 100%);
  }
  .glasses-photo {
    position: absolute;
    left: 30px;
    top: 250px;
    width: 910px;
    height: 560px;
    border-radius: 46% / 40%;
    background:
      radial-gradient(ellipse 28% 42% at 27% 52%, rgba(90, 68, 62, 0.55), transparent 75%),
      radial-gradient(ellipse 28% 42% at 73% 52%, rgba(90, 68, 62, 0.55), transparent 75%),
      radial-gradient(ellipse 60% 55% at 50% 50%, var(--photo-warm), var(--photo-deep) 70%, transparent 100%);
    opacity: 0.85;
  }
  .accent-bar {
    position: absolute;
    left: 127px;
    top: 159px;
    width: 705px;
    height: 56px;
    background: var(--promo-red);
  }
  .headline {
    position: absolute;
    left: 0;
    width: 962px;
    text-align: center;
    font-family: "Archivo Black", "Arial Black", sans-serif;
    color: var(--headline-white);
    line-height: 1;
    white-space: nowrap;
  }
  .headline--count {
    top: 268px;
    font-size: 262px;
    letter-spacing: -4px;
    padding-left: 22px;
  }
  .headline--product {
    top: 528px;
    font-size: 150px;
    letter-spacing: 0;
    padding-left: 10px;
  }
  .promo-band {
    position: absolute;
    left: 73px;
    top: 808px;
    width: 788px;
    height: 137px;
    background: var(--promo-red);
  }
  .promo-band__text {
    position: absolute;
    left: 105px;
    top: 842px;
    font-family: "Anton", "Impact", sans-serif;
    font-size: 66px;
    line-height: 1.1;
    letter-spacing: 7px;
    word-spacing: 14px;
    color: var(--promo-yellow);
    white-space: nowrap;
  }
  .promo-band__mark {
    font-size: 80px;
    vertical-align: top;
    position: relative;
    top: -10px;
    margin-left: -2px;
  }
  .sticker {
    position: absolute;
    left: 692px;
    top: 709px;
    width: 270px;
    height: 270px;
  }
</style>
</head>
<body>
  <main class="poster">
    <div class="poster__backdrop"></div>
    <div class="glasses-photo" role="img" aria-label="Dark, softly lit photograph of eyeglasses resting on an open book"></div>

    <div class="accent-bar"></div>

    <h1 class="headline headline--count">2 PAIR</h1>
    <h2 class="headline headline--product">PACKAGES</h2>

    <div class="promo-band"></div>
    <p class="promo-band__text">NOW AVAILABLE<span class="promo-band__mark">*</span></p>

    <svg class="sticker" viewBox="0 0 270 270" aria-label="Conditions apply sticker">
      <defs>
        <radialGradient id="stickerFace" cx="45%" cy="55%" r="60%">
          <stop offset="0%" stop-color="#ffffff"/>
          <stop offset="80%" stop-color="#ececec"/>
          <stop offset="100%" stop-color="#cfcfcf"/>
        </radialGradient>
        <linearGradient id="stickerCurl" x1="0" y1="0" x2="0" y2="1">
          <stop offset="0%" stop-color="#9a9a9a"/>
          <stop offset="60%" stop-color="#e6e6e6"/>
          <stop offset="100%" stop-color="#ffffff"/>
        </linearGradient>
      </defs>
      <circle cx="135" cy="135" r="120" fill="rgba(0,0,0,0.35)" transform="translate(4 6)"/>
      <path d="M 60 40 A 120 120 0 1 0 232 62 Q 180 70 140 48 Q 100 30 60 40 Z" fill="url(#stickerFace)"/>
      <path d="M 60 40 Q 100 30 140 48 Q 180 70 232 62 Q 200 22 150 18 Q 100 14 60 40 Z" fill="url(#stickerCurl)"/>
      <g transform="rotate(8 135 135)" font-family="Archivo Black, Arial Black, sans-serif" fill="var(--sticker-ink)" text-anchor="middle">
        <text x="133" y="126" font-size="26">*CONDITIONS</text>
        <text x="128" y="156" font-size="26">APPLY</text>
      </g>
    </svg>
  </main>
</body>
</html>
```